Quillmont Energy b-card redesign

I would like to redesign the card (and power point template) for quillmont energy. We are a developer/owner/operator of high-tech biomass gasification power plants. We take ag waste like nut shells or fruit pits and convert that into electricity in the 1/2 - 3 MW range. I would like to change our company color from red to golden gate bridge orange (C=0,M=69,,Y=100,B=6).

```html
<!DOCTYPE html>
<html lang="en">
<head>
<meta charset="utf-8">
<title>Quillmont Energy business card</title>
<link rel="stylesheet" href="https://fonts.googleapis.com/css2?family=Exo+2:wght@400;600;700&display=swap">
<style>
  :root {
    --stage: #9a9b9d;
    --card: #ffffff;
    --card-shade: #e9eaeb;
    --accent: #f04a00;
    --ink: #232323;
    --band: #2b2b2b;
  }
  * { margin: 0; padding: 0; box-sizing: border-box; }
  html, body { width: 1200px; height: 894px; overflow: hidden; }
  body {
    background: var(--stage);
    font-family: "Exo 2", sans-serif;
    color: var(--ink);
    position: relative;
  }
  .card {
    position: absolute;
    top: 290px;
    width: 540px;
    height: 315px;
    overflow: hidden;
    box-shadow: 0 6px 18px rgba(0,0,0,0.25);
  }
  .card--back {
    left: 50px;
    background: linear-gradient(120deg, var(--card-shade) 0%, var(--card) 45%, var(--card-shade) 100%);
  }
  .card--front { left: 610px; background: var(--card); }

  .band {
    position: absolute;
    right: 0;
    background: var(--band);
    border-radius: 34px 0 0 34px;
  }
  .card--back .band { left: 330px; top: 112px; height: 66px; }
  .card--front .band { left: 380px; top: 170px; height: 76px; border-radius: 38px 0 0 38px; }

  .holder { position: absolute; left: 40px; top: 30px; }
  .holder__name { font-size: 21px; font-weight: 700; letter-spacing: 0.5px; }
  .holder__role { font-size: 9px; letter-spacing: 1.2px; text-transform: uppercase; margin-top: 1px; }

  .rule { position: absolute; left: 40px; height: 2px; background: var(--accent); }
  .rule--name { top: 74px; width: 200px; }
  .rule--contacts { top: 186px; width: 260px; }
  .rule--foot1 { top: 262px; width: 330px; }
  .rule--foot2 { top: 288px; width: 330px; }

  .contacts { position: absolute; left: 40px; top: 86px; list-style: none; }
  .contacts li { display: flex; font-size: 13.5px; line-height: 22px; letter-spacing: 0.6px; }
  .contacts__label { width: 70px; color: var(--accent); }
  .contacts__value { color: var(--ink); }

  .address {
    position: absolute; left: 40px; top: 198px;
    display: flex; align-items: center; gap: 10px;
    font-size: 13.5px; letter-spacing: 0.8px;
  }
  .address svg { width: 14px; height: 19px; color: var(--accent); }

  .brand {
    position: absolute; left: 60px; top: 70px;
    display: flex; align-items: center; gap: 10px;
  }
  .brand__dot { width: 12px; height: 12px; border-radius: 50%; background: var(--accent); }
  .brand__name {
    font-size: 30px; font-weight: 600; letter-spacing: 2px;
    text-transform: uppercase; color: var(--accent);
  }
</style>
</head>
<body>
  <section class="card card--back" aria-label="Card back with contact details">
    <div class="holder">
      <p class="holder__name">Dorian Vale</p>
      <p class="holder__role">General Manager</p>
    </div>
    <div class="rule rule--name"></div>
    <ul class="contacts">
      <li><span class="contacts__label">Phone:</span><span class="contacts__value">014 552 8830</span></li>
      <li><span class="contacts__label">Fax:</span><span class="contacts__value">014 552 8830</span></li>
      <li><span class="contacts__label">Email:</span><span class="contacts__value">hello@quillmont.com</span></li>
      <li><span class="contacts__label">website:</span><span class="contacts__value">www.quillmontenergy.com</span></li>
    </ul>
    <div class="rule rule--contacts"></div>
    <p class="address">
      <svg viewBox="0 0 14 19" aria-hidden="true"><path d="M7 0C3.1 0 0 3.1 0 7c0 5 7 12 7 12s7-7 7-12c0-3.9-3.1-7-7-7z" fill="currentColor"/><circle cx="7" cy="7" r="2.6" fill="#fff"/></svg>
      27 9th floor, Harbor Crest Road QME
    </p>
    <div class="rule rule--foot1"></div>
    <div class="rule rule--foot2"></div>
    <div class="band"></div>
  </section>

  <section class="card card--front" aria-label="Card front with company name">
    <div class="brand">
      <span class="brand__dot"></span>
      <span class="brand__name">Quillmont Energy</span>
    </div>
    <div class="band"></div>
  </section>
</body>
</html>
```